Dietary supplement, Clean and simple.

Hi,
I’d like to talk about the project,

About us:
We are a dietary supplement (Vitamins, Minerals, amino acids etc.) company.
The goal is to have about 25 products at the end of this year. However, for this goal to be achieved we need a good label design to make our products represent our company values.
I’ll be here every day supporting your questions, we are fully committed to making the highest/best quality/customer experience possible.

About the design and our values:
- Professional (We are in the industry of professionalism and expertise. I would love to show we are competent at this, Id. Like to have the labels looks like we have done our research.)
- Efficient (White spacing, good use of the space available.)
- Simple (Straight forward, in 5 seconds they have to know what the product they have is/how functions. We’re trying to simplify it for the consumer.
- No distractions (the only visually “distracting” factor can be the vector art.)

The guidelines:
The goal is to have a universal design, with one element that changes (Vector art). I’ll attach a file/multiple files I think can show some visuals on what I’m looking for, and what parts of the design I think are good/bad.

Label size: 69x155mm (Front is 77.5mm)

Design whatever you think fits our image. You’re the design expert, all I care about is that it fits our company standards/image.

Use this color/font.
Font: Sans Serif
Main company color is Mind green #237D62 (Use this color for something in the design.)

What I thought would be cool/might looks ugly, who knows:
1. The front of the label: Should have 1 vector art, preferably in the top right corner. (That looks good in multiple colors. The vector can have multiple areas to color, I would prefer 2 main colors in the vector art. The interchangeable colors are used for multiple kinds of products.)
2. Text/product information on the left. The text that will have to be displayed:
- Product name for instance “Magnesium + B6”
- Description for the product for instance “Magnesium with ginger taste”
- Company name or logo. (Add ® behind it. We are soon to be trademark registered.)
3. We need to show the "daily intake" amount on the front and also the amount in the complete bottle. For instance, “Daily intake 1 capsule, 60 capsules”.
• You don’t have to design the backside of the label. After I chose a design, I’d like to chat and give specific information on what areas need to be assigned where. (Too complex because of the law.)
Updates

Hi, Please make the deadline 31 days total. I want designers to have the time to design. And not be rushed to finish it.

I want to extend the deadline because i feel like a slightly more medical look would be interesting. Hope you can come up with something!!

Target Market(s)

Dietary supplement consumers

Industry/Entity Type

Dietary supplements

Font styles to use
Sans Serif

Colors

Designer to choose colors to be used in the design.

Requirements
Must have
• Trademark icon "®" has to be at the top right after the company logo(text of logo)/name.

```html
<!DOCTYPE html>
<html lang="en">
<head>
<meta charset="utf-8">
<title>Linden Vale – Magnesium label</title>
<link rel="stylesheet" href="https://fonts.googleapis.com/css2?family=Montserrat:wght@400;500;600;700&display=swap">
<style>
  :root {
    --paper: #ffffff;
    --peach: #fdd3a3;
    --tan-side: #d09068;
    --plum: #52193f;
    --copper: #c67d4c;
    --copper-text: #c98b63;
    --mind-green: #237d62;
  }
  html, body {
    margin: 0;
    padding: 0;
    width: 1200px;
    height: 535px;
    overflow: hidden;
    background: var(--paper);
  }
  .label-canvas {
    display: block;
    width: 1200px;
    height: 535px;
    font-family: "Montserrat", sans-serif;
  }
  .band { fill: var(--peach); }
  .side-tab { fill: var(--tan-side); }
  .title-field { fill: var(--plum); }
  .badge-ring { fill: var(--paper); }
  .badge-core { fill: var(--copper); }
  .badge-rule { stroke: var(--paper); stroke-width: 3; }
  .weight-disc { fill: var(--paper); }

  .brand-name { fill: var(--mind-green); font-weight: 700; font-size: 38px; letter-spacing: 1px; }
  .product-name { fill: var(--copper-text); font-weight: 700; font-size: 62px; letter-spacing: 1px; }
  .product-desc { fill: var(--paper); font-weight: 500; font-size: 21px; letter-spacing: 0.3px; }
  .intake-lead { fill: var(--paper); font-weight: 400; font-size: 19px; }
  .intake-dose { fill: var(--paper); font-weight: 700; font-size: 26px; }
  .pack-count { fill: var(--paper); font-weight: 700; font-size: 68px; }
  .net-weight { fill: var(--copper); font-weight: 700; font-size: 24px; }
  .net-unit { fill: var(--copper); font-weight: 600; font-size: 12px; }
</style>
</head>
<body>
<svg class="label-canvas" viewBox="0 0 1832 817" preserveAspectRatio="none" xmlns="http://www.w3.org/2000/svg">
  <rect x="455" y="0" width="915" height="817" fill="var(--paper)"/>

  <path class="band band-top" d="M455 0 H1370 V47 C1200 40 1050 75 920 75 C790 75 600 40 455 47 Z"/>
  <path class="band band-bottom" d="M455 817 V672 C600 672 720 620 830 585 L1020 585 C1130 620 1250 668 1370 668 V817 Z"/>

  <path class="side-tab side-tab-left" d="M455 148 C480 155 499 165 499 180 V670 C499 685 480 690 455 698 Z"/>
  <path class="side-tab side-tab-right" d="M1370 148 C1345 155 1326 165 1326 180 V670 C1326 685 1345 690 1370 698 Z"/>

  <text class="brand-name" x="1172" y="192" text-anchor="middle">LINDEN VALE®</text>

  <path class="title-field" d="M630 520 A294 294 0 0 1 1218 520 C1218 580 1195 605 1160 603 L1025 568 L822 568 L690 603 C650 605 630 580 630 520 Z"/>

  <text class="product-name" x="924" y="428" text-anchor="middle">MAGNESIUM</text>
  <text class="product-desc" x="924" y="450" text-anchor="middle">Magnesium with lemon taste</text>

  <g class="intake-badge">
    <circle class="badge-ring" cx="924" cy="570" r="102"/>
    <circle class="badge-core" cx="924" cy="570" r="95"/>
    <text class="intake-lead" x="926" y="530" text-anchor="middle">take daily</text>
    <text class="intake-dose" x="924" y="556" text-anchor="middle">1 CAPSULE</text>
    <line class="badge-rule" x1="848" y1="570" x2="1003" y2="570"/>
    <text class="pack-count" x="925" y="627" text-anchor="middle">60</text>
  </g>

  <g class="weight-tag">
    <circle class="weight-disc" cx="924" cy="692" r="34"/>
    <text class="net-weight" x="924" y="697" text-anchor="middle">180</text>
    <text class="net-unit" x="924" y="710" text-anchor="middle">grams</text>
  </g>
</svg>
</body>
</html>
```